Walk Beside The River

Business Card design

Target Market(s)

People who require support in the commnity

Industry/Entity Type

Mental Health Support

Contact Information for Business Card

Mental Health Support Rosalind Tavener walkbesidetheriver@mailcove.com.au 0481 637 092 PO Box 926 Wattle Creek QLD 4517

Colors
6B429C
8869AF
B7A5CE
E3DAEB
F3F0F8

Requirements
Must have
• Logo & details listed above
Should not have
• No red or orange

```html
<!DOCTYPE html>
<html lang="en">
<head>
<meta charset="utf-8">
<title>Walk Beside The River – Business Card</title>
<link rel="stylesheet" href="https://fonts.googleapis.com/css2?family=Open+Sans:wght@400;600;700;800&display=swap">
<style>
  :root {
    --purple: #6B429C;
    --purple-mid: #8869AF;
    --purple-soft: #B7A5CE;
    --purple-dark: #4E2F7A;
    --lilac: #E3DAEB;
    --mist: #F3F0F8;
    --yellow: #EFE62A;
    --ink: #1E1A24;
    --white: #FFFFFF;
  }
  * { box-sizing: border-box; margin: 0; padding: 0; }
  html, body { width: 1200px; height: 780px; overflow: hidden; }
  body {
    background: var(--mist);
    font-family: "Open Sans", Arial, sans-serif;
    display: flex;
    align-items: center;
    justify-content: center;
    gap: 40px;
  }
  .card {
    position: relative;
    width: 540px;
    height: 310px;
    border-radius: 20px;
    overflow: hidden;
    border-bottom: 4px solid var(--yellow);
    box-shadow: 0 10px 30px rgba(78, 47, 122, 0.18);
  }

  /* Back */
  .card-back { background: var(--purple); }
  .card-back .pattern-field {
    position: absolute; inset: 0;
    background: linear-gradient(160deg, var(--purple-mid) 0%, var(--purple) 45%, var(--purple-dark) 100%);
  }
  .card-back .brand {
    position: absolute; right: 34px; top: 118px;
    display: flex; align-items: center; gap: 10px;
  }
  .brand-dot {
    width: 22px; height: 22px; border-radius: 50%;
    background: var(--yellow);
    flex: none;
  }
  .brand-name { white-space: nowrap; }
  .card-back .brand-name {
    color: var(--white); font-weight: 600; font-size: 13px; letter-spacing: 0.04em;
  }

  /* Front */
  .card-front { background: var(--white); }
  .card-front .shapes { position: absolute; inset: 0; width: 100%; height: 100%; }
  .person {
    position: absolute; right: 62px; top: 22px; text-align: right;
  }
  .person-name {
    color: var(--purple); font-weight: 800; font-size: 30px; line-height: 1.05; white-space: nowrap;
  }
  .person-role {
    color: var(--ink); font-size: 14px; margin-top: 2px;
  }
  .card-front .brand {
    position: absolute; left: 28px; top: 92px;
    display: flex; align-items: center; gap: 12px;
  }
  .card-front .brand-dot {
    width: 62px; height: 62px; background: var(--purple);
  }
  .card-front .brand-name {
    color: var(--purple); font-weight: 600; font-size: 15px; line-height: 1.25;
  }
  .details {
    position: absolute; left: 28px; top: 172px;
    color: var(--ink); font-size: 14px; line-height: 1.5;
  }
  .contact-line { display: flex; align-items: center; gap: 8px; white-space: nowrap; }
  .contact-line svg { width: 14px; height: 14px; flex: none; fill: var(--purple); }
</style>
</head>
<body>

  <section class="card card-back" aria-label="Card back">
    <div class="pattern-field" role="img" aria-label="Purple field with a repeating star pattern fading lighter toward the top"></div>
    <div class="brand">
      <span class="brand-dot"></span>
      <span class="brand-name">Walk Beside The River</span>
    </div>
  </section>

  <section class="card card-front" aria-label="Card front">
    <svg class="shapes" viewBox="0 0 540 310" preserveAspectRatio="none" aria-hidden="true">
      <rect class="corner-tab" x="500" y="0" width="40" height="34" fill="var(--purple)"/>
      <path class="wave" d="M540,92 C470,108 432,160 412,220 C392,282 300,302 150,310 L540,310 Z" fill="var(--purple)"/>
      <path class="swoosh" d="M112,292 C230,298 330,282 384,228 C345,288 240,306 128,304 Z" fill="var(--yellow)"/>
    </svg>

    <div class="person">
      <div class="person-name">Mirela Kostovska</div>
      <div class="person-role">CEO/Director</div>
    </div>

    <div class="brand">
      <span class="brand-dot"></span>
      <span class="brand-name">Walk Beside The River</span>
    </div>

    <div class="details">
      <div class="service">Mental Health Support</div>
      <div class="contact-person">Rosalind Tavener</div>
      <div class="contact-line">
        <svg viewBox="0 0 24 24"><path d="M6.6 10.8a15.1 15.1 0 0 0 6.6 6.6l2.2-2.2a1 1 0 0 1 1-.25 11.4 11.4 0 0 0 3.6.57 1 1 0 0 1 1 1V20a1 1 0 0 1-1 1A17 17 0 0 1 3 4a1 1 0 0 1 1-1h3.5a1 1 0 0 1 1 1c0 1.25.2 2.45.57 3.57a1 1 0 0 1-.25 1z"/></svg>
        <span>0481 637 092</span>
      </div>
      <div class="contact-line">
        <svg viewBox="0 0 24 24"><path d="M3 5h18a1 1 0 0 1 1 1v12a1 1 0 0 1-1 1H3a1 1 0 0 1-1-1V6a1 1 0 0 1 1-1zm9 7.2L4.3 7H19.7zM4 8.6V17h16V8.6l-8 5.4z"/></svg>
        <span>walkbesidetheriver@mailcove.com.au</span>
      </div>
      <div class="contact-line">
        <svg viewBox="0 0 24 24"><path d="M12 2a7 7 0 0 1 7 7c0 5-7 13-7 13S5 14 5 9a7 7 0 0 1 7-7zm0 4.5A2.5 2.5 0 1 0 12 11.5 2.5 2.5 0 0 0 12 6.5z"/></svg>
        <span>PO Box 926 Wattle Creek QLD 4517</span>
      </div>
    </div>
  </section>

</body>
</html>
```